Car Detailing Brochure/PriceList

Looking for a nicely designed Brochure/Price sheet that can be displayed on the website and Murmurly sites which details the different service stages available to potential customers

Target Market(s)

People in the local area who need paint enhancement and correction

Industry/Entity Type

Car Detailing

Requirements
Must have
• Reader Friendly, Informative, pictures (lots on Murmurly/Website that can be used) would like to see nicely imbedded pictures relating to stages etc
Nice to have
• Luxury design following company branding with logo/colours etc https://www.velvorashine.uk/services

```html
<!DOCTYPE html>
<html lang="en">
<head>
<meta charset="utf-8">
<title>Velvora Shine – Detailing Price List</title>
<link rel="stylesheet" href="https://fonts.googleapis.com/css2?family=Poppins:wght@400;500;600&family=Roboto+Slab:wght@400;500&display=swap">
<style>
  :root {
    --backdrop: #c9c9c9;
    --paper: #fbfbfb;
    --ink: #1c1c1c;
    --accent: #d6471b;
    --muted: #9b9b9b;
    --rule: #d4dce5;
    --copper-dark: #4a200c;
    --copper-mid: #a4420f;
    --copper-glow: #f29a1c;
    --figure-tone: #e3e3e3;
  }
  * { box-sizing: border-box; margin: 0; padding: 0; }
  html, body { width: 1200px; height: 900px; overflow: hidden; }
  body {
    background: var(--backdrop);
    font-family: "Poppins", sans-serif;
    color: var(--ink);
    display: flex;
    align-items: center;
    justify-content: center;
  }
  .price-sheet {
    position: relative;
    width: 600px;
    height: 842px;
    background: var(--paper);
    box-shadow: 0 10px 28px rgba(0,0,0,.25);
    overflow: hidden;
  }
  .header-band {
    position: absolute;
    inset: 0 0 auto 0;
    height: 122px;
    background: linear-gradient(90deg, var(--copper-dark) 0%, var(--copper-mid) 22%, #d0600f 38%, var(--copper-glow) 50%, #c9560f 62%, var(--copper-mid) 80%, var(--copper-dark) 100%);
  }
  .header-wordmark {
    position: absolute;
    top: 24px; left: 0; right: 0;
    text-align: center;
    font-family: "Poppins", sans-serif;
    font-weight: 600;
    font-size: 44px;
    letter-spacing: 1px;
    color: #161616;
    line-height: 56px;
  }
  .faint-figure {
    position: absolute;
    left: 482px; top: 612px;
    width: 78px; height: 168px;
    border-radius: 30px 30px 6px 6px;
    background: linear-gradient(180deg, #e8e8e8, var(--figure-tone));
    z-index: 1;
  }
  .content-panel {
    position: absolute;
    top: 80px; left: 25px; right: 25px; bottom: 16px;
    background: var(--paper);
    padding: 26px 32px 0 32px;
  }
  .content-inner { position: relative; z-index: 2; }
  .brand-row { display: flex; align-items: center; gap: 12px; margin-bottom: 14px; padding-left: 10px; }
  .brand-dot {
    width: 32px; height: 32px; border-radius: 50%;
    border: 3px solid var(--accent);
    flex: none;
  }
  .brand-name {
    font-family: "Roboto Slab", serif;
    font-weight: 400;
    font-size: 22px;
    color: var(--accent);
    letter-spacing: .5px;
  }
  .stage { margin-bottom: 14px; }
  .stage-tag {
    display: inline-block;
    margin-left: 10px;
    background: var(--accent);
    color: #fff;
    font-size: 7.5px;
    font-weight: 500;
    padding: 1px 18px 1px 4px;
  }
  .stage-box {
    border: 1px solid var(--rule);
    padding: 8px 14px 4px 14px;
    margin-top: 3px;
  }
  .stage-copy {
    font-size: 9.2px;
    line-height: 1.3;
    text-align: justify;
  }
  .prices { display: flex; align-items: flex-start; margin-top: 2px; }
  .prices-label {
    color: var(--accent);
    font-size: 12.5px;
    width: 58px;
    flex: none;
    line-height: 1.2;
  }
  .price-list { list-style: none; font-size: 9.2px; line-height: 1.3; width: 180px; flex: none; }
  .price-list span { color: var(--accent); }
  .price-note {
    font-size: 8.8px;
    line-height: 1.3;
    color: var(--muted);
    margin-top: 13px;
    width: 170px;
  }
  .upgrades { margin-top: 8px; max-width: 425px; }
  .upgrades-title { color: var(--accent); font-size: 14.5px; font-weight: 500; margin-bottom: 4px; }
  .upgrades p { font-size: 9.2px; line-height: 1.35; }
  .upgrades .label, .upgrades .cost { color: var(--accent); }
  .footer-strip {
    position: absolute;
    left: 0; right: 0; bottom: 0;
    height: 16px;
    background: linear-gradient(90deg, #5a1d0b, var(--accent) 50%, #5a1d0b);
  }
</style>
</head>
<body>
  <main class="price-sheet">
    <div class="header-band"></div>
    <div class="header-wordmark">VELVORA SHINE</div>

    <section class="content-panel">
      <div class="content-inner">
        <div class="brand-row">
          <div class="brand-dot"></div>
          <h1 class="brand-name">VELVORA SHINE</h1>
        </div>

        <article class="stage">
          <span class="stage-tag">Stage One</span>
          <div class="stage-box">
            <p class="stage-copy">Ideally suited to Brand new or exceptionally well-maintained vehicles. This Stage will remove light swirl marks, marring and micro scratches typically found in new car preparation or from home car washing methods. It includes; full inspection and prewash, wheels cleaned, snow foam, decontamination process, single stage machine polish, glass cleaned and a Liquid wax finish. This will give up to 6 months protection and takes between 1 – 1.5 days.</p>
            <div class="prices">
              <div class="prices-label">PRICES:</div>
              <ul class="price-list">
                <li>Small car <span>£240,</span></li>
                <li>Medium car <span>£270,</span></li>
                <li>Large car <span>£300,</span></li>
                <li>4x4s/pickups/vans from <span>£350</span></li>
              </ul>
              <p class="price-note">*Upgrade to a hard wax finish with up to 12 months protection + interior valet from £130</p>
            </div>
          </div>
        </article>

        <article class="stage">
          <span class="stage-tag">Stage One</span>
          <div class="stage-box">
            <p class="stage-copy">This is our most popular package and will suit most vehicles. It includes everything from stage 1 plus a 2-stage polish that will address light scratches and imperfection, oxidation and begin to correct and level the paint surface resulting in an exceptional shine. Combined with a hard wax coating this will not only lock in the shine for longer but also make home cleaning and maintenance easier and more effective. This will give 6 -9 months protection and takes from 2.5 days</p>
            <div class="prices">
              <div class="prices-label">PRICES:</div>
              <ul class="price-list">
                <li>Small car <span>£400,</span></li>
                <li>Medium car <span>£430,</span></li>
                <li>Large car <span>£460,</span></li>
                <li>4x4/pickups/vans from <span>£500</span></li>
              </ul>
              <p class="price-note">*Upgrade to a ceramic coating with 2 - 3 years protection + interior valet from £250</p>
            </div>
          </div>
        </article>

        <article class="stage">
          <span class="stage-tag">Stage Three</span>
          <div class="stage-box">
            <p class="stage-copy">This is our luxury level paint correction. It includes everything from stage 2 plus a 3 stage polish that will provide a glorious, better than new, mirror like shine. The 3 stage polish will remove medium to heavy scratches and will level the paint to give that wet look glossy finish you never thought possible. For the ultimate protection we recommend taking advantage of a professional grade ceramic coating which when applied will lock in that glossy finish and provide the longest possible protection. A full valet is included on this stage and with basic hard wax your protection will last up to 12 months and takes from 3.5 days.</p>
            <div class="prices">
              <div class="prices-label">PRICES:</div>
              <ul class="price-list">
                <li>Small car <span>£600,</span></li>
                <li>Medium car <span>£630,</span></li>
                <li>Large car <span>£660,</span></li>
                <li>4x4/pickups/vans from <span>£700</span></li>
              </ul>
              <p class="price-note">*Interior valet included, add ceramic coating with 2 - 3 years protection from £200</p>
            </div>
          </div>
        </article>

        <div class="upgrades">
          <h2 class="upgrades-title">Upgrades available on all stages;</h2>
          <p><span class="label">Hard Carnauba Wax Protection;</span> 1 year from <span class="cost">£70</span></p>
          <p><span class="label">Ceramic Coating;</span> 2-3 years paint protection from £200, Ceramic Wheel Protection from £100, Ceramic Leather protection from £100, Glass protection from £40</p>
          <p><span class="label">Interior valet;</span> Full deep steam clean including Carpets, Mats, leather cleaner, Plastics and sanitisation from <span class="cost">£80</span></p>
        </div>
      </div>
    </section>

    <div class="faint-figure" role="img" aria-label="Faint brand figure decoration"></div>
    <div class="footer-strip" role="img" aria-label="Copper textured footer pattern"></div>
  </main>
</body>
</html>
```